Tradelume.ai

Australian based application building technology company. website (tradelume.ai) servicing the retail and shopping industries, IoT
Similar services to https://vextrio.com/.
Logo attached

Target Market(s)

Technology Retail

Industry/Entity Type

It Company

Number of Pages Required

2 page

Font styles to use
Other font styles liked:
• We will supply

Colors
ec1f27

Requirements
Must have
• responsive, extra small, small, medium, large, wide
Nice to have
• Modern, sophisticated, current and ON trende
Should not have
• Over saturation, keep it simple, smart and easy navigation

```html
<!DOCTYPE html>
<html lang="en">
<head>
<meta charset="utf-8">
<title>Tradelume – Real Time Shopping Online Experiences</title>
<link rel="stylesheet" href="https://fonts.googleapis.com/css2?family=Montserrat:wght@500;600;700&family=Roboto:wght@400;500;700&family=Lato:wght@400&display=swap">
<style>
:root{
  --brand:#ec1f27;
  --brand-dark:#c0161d;
  --ink:#222;
  --muted:#8a8a8a;
  --grey-bg:#f4f4f4;
  --footer:#1a1a1a;
  --white:#fff;
}
*{box-sizing:border-box;margin:0;padding:0}
html,body{width:1200px;height:2727px;overflow:hidden}
body{font-family:"Lato",sans-serif;color:var(--ink);background:var(--white);position:relative}
.abs{position:absolute}

/* header */
.site-header{position:absolute;left:0;top:0;width:1200px;height:68px;background:var(--white)}
.brand{position:absolute;left:100px;top:19px;display:flex;align-items:center;gap:10px;font-family:"Roboto",sans-serif;font-weight:500;font-size:24px;color:var(--brand);letter-spacing:.5px}
.brand .mark{width:22px;height:22px;border-radius:50%;background:var(--brand)}
.main-nav{position:absolute;top:24px;left:0;width:1200px;font-family:"Roboto",sans-serif;font-weight:500;font-size:12px;letter-spacing:.4px}
.main-nav a{position:absolute;color:var(--ink);text-decoration:none;top:3px}
.main-nav .cta{left:1000px;top:-2px;width:102px;height:24px;background:var(--brand);color:var(--white);display:flex;align-items:center;justify-content:center;font-size:11.5px}

/* hero */
.hero{position:absolute;left:0;top:68px;width:1200px;height:568px;background:linear-gradient(100deg,#5b4a3c 0%,#7d6c57 35%,#6f7460 60%,#8c9383 100%)}
.hero-shade{position:absolute;inset:0;background:rgba(0,0,0,.28)}
.hero h1{position:absolute;top:232px;width:100%;text-align:center;font-family:"Roboto",sans-serif;font-weight:500;font-size:35px;color:var(--white);letter-spacing:.3px}
.hero .sub{position:absolute;top:296px;width:100%;text-align:center;font-family:"Roboto",sans-serif;font-size:27px;color:var(--white)}
.btn-outline-light{position:absolute;left:458px;top:368px;width:294px;height:58px;border:2px solid var(--white);color:var(--white);display:flex;align-items:center;justify-content:center;font-family:"Roboto",sans-serif;font-weight:500;font-size:22px;letter-spacing:.5px}
.dots{position:absolute;top:530px;left:578px;display:flex;gap:5px}
.dots span{width:11px;height:11px;border-radius:50%;border:2px solid var(--white)}
.dots span.on{background:var(--brand);border-color:var(--brand)}

/* text styles */
.section-title{font-family:"Montserrat",sans-serif;font-weight:700;font-size:25px;line-height:42px;color:var(--brand-dark);letter-spacing:.6px}
.body-copy{font-family:"Lato",sans-serif;font-size:11px;line-height:20px;color:var(--muted)}
.btn-outline{position:absolute;border:2px solid var(--brand);color:var(--brand-dark);display:flex;align-items:center;justify-content:center;font-family:"Montserrat",sans-serif;font-weight:500;font-size:16px;letter-spacing:.6px}

/* engagement */
.engagement{position:absolute;left:0;top:636px;width:1200px;height:504px;background:var(--white)}

/* analytics */
.analytics{position:absolute;left:0;top:1140px;width:1200px;height:765px;background:var(--grey-bg)}
.analytics .section-title{position:absolute;top:48px;width:100%;text-align:center;font-size:26px}
.analytics .lead{position:absolute;top:97px;width:100%;text-align:center;font-family:"Montserrat",sans-serif;font-weight:500;font-size:23px;color:var(--brand-dark)}
.features{position:absolute;top:646px;left:0;width:1200px}
.feature{position:absolute;display:flex;align-items:center;gap:22px;font-family:"Roboto",sans-serif;font-size:19px;line-height:25px;color:var(--ink)}

/* personal shopper */
.shopper{position:absolute;left:0;top:1905px;width:1200px;height:404px;background:var(--white)}
.checklist{position:absolute;left:198px;top:258px;list-style:none;font-family:"Lato",sans-serif;font-size:12px;color:var(--muted)}
.checklist li{height:29px;display:flex;align-items:center;gap:10px}
.checklist li::before{content:"";width:7px;height:7px;border-radius:50%;border:1.5px solid var(--muted)}

/* cta */
.cta-band{position:absolute;left:0;top:2309px;width:1200px;height:266px;background:var(--brand);color:var(--white);text-align:center;font-family:"Roboto",sans-serif}
.cta-band h2{position:absolute;top:34px;width:100%;font-weight:500;font-size:38px}
.cta-band p{position:absolute;top:96px;width:100%;font-size:16.5px;font-weight:500;line-height:29px}
.cta-band .btn-outline-light{left:509px;top:181px;width:182px;height:47px;font-size:19px}

/* footer */
.site-footer{position:absolute;left:0;top:2575px;width:1200px;height:152px;background:var(--footer);font-family:"Roboto",sans-serif;color:var(--white)}
.footer-nav a{position:absolute;top:33px;color:var(--white);text-decoration:none;font-size:14px;font-weight:500}
.footer-brand{position:absolute;top:86px;left:0;width:100%;display:flex;justify-content:center;align-items:center;gap:10px;font-size:28px;font-weight:500;letter-spacing:.6px}
.footer-brand .mark{width:26px;height:26px;border-radius:50%;background:var(--white)}
</style>
</head>
<body>

<header class="site-header">
  <div class="brand"><span class="mark"></span>TRADELUME</div>
  <nav class="main-nav">
    <a style="left:688px">PRODUCTS</a>
    <a style="left:797px">RESOURCES</a>
    <a style="left:909px">SUPPORT</a>
    <a class="cta">GET STARTED</a>
  </nav>
</header>

<section class="hero">
  <div class="abs" style="inset:0;background:linear-gradient(100deg,#4e3f33,#7a6a55 40%,#6b735e 65%,#9aa08f)" role="img" aria-label="Woman at a café table smiling while shopping on her phone"></div>
  <div class="hero-shade"></div>
  <h1>REAL TIME SHOPPING ONLINE EXPERIENCES</h1>
  <p class="sub">Bridging Online &amp; Real Time Shopping</p>
  <a class="btn-outline-light">SEE THE EXPERIENCE</a>
  <div class="dots"><span class="on"></span><span></span><span></span></div>
</section>

<section class="engagement">
  <div class="abs" style="left:122px;top:30px;width:443px;height:425px;background:linear-gradient(150deg,#f3f3f3,#d6d6d6 55%,#b9b9b9);border-radius:24px" role="img" aria-label="Smartphone showing a store app page for sunglasses"></div>
  <h2 class="section-title abs" style="left:585px;top:103px">ENTRY TO EXIT ENGAGEMENT MAP,<br>PROMOTE AND PROFILE LIVE IN STORE</h2>
  <p class="body-copy abs" style="left:587px;top:204px;width:516px">Lorem Ipsum is simply dummy text of the printing and typesetting industry. Lorem Ipsum has been the industry's standard dummy text ever since the 1500s, when an unknown printer took a galley of type and scrambled it to make a type specimen book. It has survived not only five centuries Lorem Ipsum is simply dummy text of the printing and typesetting industry. Lorem Ipsum has been the industry's standard dummy text ever since the 1500s, when an unknown printer.</p>
  <a class="btn-outline" style="left:586px;top:335px;width:228px;height:41px">UPGRADE YOUR APP</a>
</section>

<section class="analytics">
  <h2 class="section-title">ONLINE CAPABILITIES &amp; ANALYTICS</h2>
  <p class="lead">Enhance Your Customers Instore Shop At Specific Products or Places</p>
  <div class="abs" style="left:395px;top:167px;width:411px;height:321px;background:linear-gradient(180deg,#1c1c1c 0%,#1c1c1c 10%,#f6e27a 30%,#f2d95a 70%,#c8c8c8 80%,#e2e2e2 100%);border-radius:10px" role="img" aria-label="Desktop monitor showing a product page with eyeglasses"></div>
  <p class="body-copy abs" style="left:113px;top:528px;width:974px;text-align:center">Lorem Ipsum is simply dummy text of the printing and typesetting industry. Lorem Ipsum has been the industry's standard dummy text ever since the 1500s, when an unknown printer took a galley of type and scrambled it to make a type specimen book. It has survived not only five centuries Lorem Ipsum is simply dummy text of the printing and typesetting industry. Lorem Ipsum has been the industry's standard dummy text ever since the 1500s, when an unknown printer took a galley of type and scrambled it to make a type specimen book. It has survived not only five centuries Lorem Ipsum is simply dummy text of the printing and typesetting industry</p>
  <div class="features">
    <div class="feature" style="left:122px">
      <svg width="38" height="38" viewBox="0 0 24 24" fill="none" stroke="#222" stroke-width="1.6" stroke-linejoin="round"><path d="M22 2 2 10l8 3 3 9z"/><path d="M22 2 10 13"/></svg>
      <span>Map To An Exact<br>Location</span>
    </div>
    <div class="feature" style="left:488px">
      <svg width="34" height="34" viewBox="0 0 24 24" fill="none" stroke="#222" stroke-width="2"><circle cx="12" cy="12" r="10"/><path d="M12 6v6h-3"/></svg>
      <span>Promote Specific To<br>Time &amp; Place</span>
    </div>
    <div class="feature" style="left:864px">
      <svg width="36" height="34" viewBox="0 0 24 22" fill="none" stroke="#222" stroke-width="1.8"><rect x="2" y="2" width="20" height="18"/><path d="M2 7h20M2 12h20M2 16h20M8 7v13M15 7v13"/></svg>
      <span>Interact LIVE At<br>Product Level</span>
    </div>
  </div>
</section>

<section class="shopper">
  <h2 class="section-title abs" style="left:198px;top:80px">A PERSONAL SHOPPER IN EVERY<br>CUSTOMERS HAND</h2>
  <p class="body-copy abs" style="left:196px;top:173px;width:450px">Lorem Ipsum is simply dummy text of the printing and typesetting industry. Lorem Ipsum has been the industry's standard dummy text ever since the 1500s, when an unknown printer took a galley of type and scrambled.</p>
  <ul class="checklist">
    <li>Establish first contact in seconds</li>
    <li>Interact Immediately &amp; Promote</li>
    <li>Analytics For Real Time Sales</li>
  </ul>
  <div class="abs" style="left:745px;top:25px;width:205px;height:379px;background:linear-gradient(180deg,#2a2a2a 0%,#c98a5e 22%,#e8e3dd 45%,#f2f2f2 100%);border-radius:60px 60px 0 0" role="img" aria-label="Young woman in a hat and sunglasses using her smartphone"></div>
</section>

<section class="cta-band">
  <h2>Ready to get started?</h2>
  <p>If you're running a small bodega or a chain of shopping malls, contact us for a custom proposal and to learn more.<br>We're happy to help.</p>
  <a class="btn-outline-light">GET STARTED</a>
</section>

<footer class="site-footer">
  <nav class="footer-nav">
    <a style="left:354px">Company</a>
    <a style="left:481px">Shop</a>
    <a style="left:577px">News</a>
    <a style="left:676px">Jobs</a>
    <a style="left:769px">Contact Us</a>
  </nav>
  <div class="footer-brand"><span class="mark"></span>TRADELUME</div>
</footer>

</body>
</html>
```